Occasions chocolate packaging

We are looking for 7 packaging designs for bars of chocolate.

Each design needs to be different and we’re not looking for a consistent brand or branding message across the designs. Inspiration should come from gift/occasion cards. Fun, simple, bold, vibrant colours and eye catching, i.e. not vintage or just text.

The front of the packaging should have the main message on and is free of any branding. You don’t need to design the back, just simply allow the main background colour or design pattern to continue around.

These are the different designs we are after, I’ve added in some text for each to give you some guidance but feel free to play around with the message if it suits the design better.

1) Mum
‘The best mum’, ‘Best mum in the World’, ‘Number 1 Mum’

2) Dad
‘The Best Dad’, ‘Best Dad Ever’, ‘Number 1 Dad’, ‘You’re my hero Dad’

3) Husband
‘Best Husband in the World’, ‘Husband I Love You’, ‘Darling Husband’

4) Wife
‘Best Wife in the World’, ‘For my Wonderful Wife’, ‘My Beautiful Wife’

5) Congratulations
Simple one, just Congratulations

6) Thinking of you
Try and keep this neutral as it could be used for happy and sad situations.

7) Thank you
Keep this gender neutral.

Sides:
The sides need to have the following text:

FINE BELGIAN DARK CHOCOLATE
infused with Orange

Back:
The main colour of the front should continue all the way around, we will place a box with the contents and bar code on here ourselves so no need to do anything.

Dimensions:
Attached in the document, front of package is 85mm by 190mm.

The packaging is made from folded card, the first blank part is for gluing the back on to.

Reason: I'm extending the deadline as I've only received 1 design so far which has followed the brief. Although I do like it, I would like to see at least some competition...

```html
<!DOCTYPE html>
<html lang="en">
<head>
<meta charset="utf-8">
<title>Best Dad in the World – Chocolate Bar Wrapper</title>
<link rel="stylesheet" href="https://fonts.googleapis.com/css2?family=Oswald:wght@500;700&family=Open+Sans:ital,wght@0,400;0,700;1,400&display=swap">
<style>
  :root {
    --page-bg: #e8e9eb;
    --wrap-blue: #1b4fd8;
    --wrap-blue-light: #2f6ff2;
    --wrap-blue-dark: #143fb4;
    --side-blue: #1844c2;
    --ink-white: #ffffff;
    --heart-pink: #f3a1c3;
  }
  * { margin: 0; padding: 0; box-sizing: border-box; }
  html, body {
    width: 1200px;
    height: 960px;
    overflow: hidden;
    background: var(--page-bg);
  }
  .wrapper-flat {
    position: absolute;
    left: 392px;
    top: 60px;
    width: 416px;
    height: 840px;
    display: flex;
    box-shadow: 0 10px 30px rgba(0, 0, 0, 0.18);
  }
  .side-panel {
    width: 40px;
    height: 100%;
    background: linear-gradient(180deg, var(--side-blue), var(--wrap-blue-dark));
    display: flex;
    align-items: center;
    justify-content: center;
    border-right: 1px solid rgba(0, 0, 0, 0.15);
  }
  .side-text {
    writing-mode: vertical-rl;
    transform: rotate(180deg);
    font-family: "Open Sans", sans-serif;
    color: var(--ink-white);
    font-size: 19px;
    white-space: nowrap;
  }
  .side-text .side-title { font-weight: 700; font-style: italic; letter-spacing: 3.5px; }
  .side-text .side-sub {
    display: inline-block;
    font-weight: 400;
    font-size: 17px;
    letter-spacing: 2.5px;
    margin-inline-start: 18px;
  }
  .front-panel {
    position: relative;
    width: 376px;
    height: 100%;
    overflow: hidden;
    background: radial-gradient(ellipse at 50% 40%, var(--wrap-blue-light) 0%, var(--wrap-blue) 55%, var(--wrap-blue-dark) 100%);
  }
  .dad-daughter-art {
    position: absolute;
    left: 86px;
    top: 40px;
    width: 220px;
    height: 460px;
    border-radius: 14px;
    background: linear-gradient(180deg, rgba(255,255,255,0.92), rgba(255,255,255,0.78));
  }
  .heart {
    position: absolute;
    left: 244px;
    top: 438px;
    width: 102px;
    height: 90px;
    z-index: 1;
  }
  .headline {
    position: absolute;
    left: 0;
    width: 100%;
    text-align: center;
    font-family: "Oswald", sans-serif;
    color: var(--ink-white);
    line-height: 1;
    text-transform: uppercase;
    z-index: 2;
  }
  .headline-best  { top: 504px; font-size: 102px; font-weight: 700; letter-spacing: -1px; }
  .headline-dad   { top: 612px; font-size: 146px; font-weight: 700; letter-spacing: -2px; }
  .headline-world { top: 776px; font-size: 40px; font-weight: 500; letter-spacing: -1.5px; }
</style>
</head>
<body>
  <div class="wrapper-flat">
    <div class="side-panel">
      <p class="side-text"><span class="side-title">FINE BELGIAN DARK CHOCOLATE</span> <span class="side-sub">infused with Orange</span></p>
    </div>
    <div class="front-panel">
      <div class="dad-daughter-art" role="img" aria-label="White silhouette of a father holding up his young daughter by the hands"></div>
      <svg class="heart" viewBox="0 0 104 92" aria-hidden="true">
        <path d="M52 88 C20 66 2 50 2 28 C2 12 14 2 28 2 C40 2 48 9 52 18 C56 9 64 2 76 2 C90 2 102 12 102 28 C102 50 84 66 52 88 Z" fill="var(--heart-pink)"/>
      </svg>
      <p class="headline headline-best">Best</p>
      <p class="headline headline-dad">Dad</p>
      <p class="headline headline-world">In the World</p>
    </div>
  </div>
</body>
</html>
```